Harborline Renewal Business Card Design

Professional and clean design. The design colors should flow with the logo. Two-sided card with the website on the back which is:

www.HarborlineRenewal.example.

"Specializing in Water Damage Restoration"

On the front I need the name, email, phone, and logo.

Name: Darnell Quisby
Email: Darnell@HarborlineRenewal.example
Phone: 555-318-2046 for now

I only have the Preview and Thumbnail right now but should have the source files uploaded within a day or two.

Target Market(s)

Flood victims, home owners with water damage from busted pipes etc...

Industry/Entity Type

Business

Contact Information for Business Card

Name: Darnell Quisby

Font styles to use
Serif
Sans Serif

Requirements
Must have
• Business Card Details Info

```html
<!DOCTYPE html>
<html lang="en">
<head>
<meta charset="utf-8">
<title>Harborline Renewal Business Card</title>
<link rel="stylesheet" href="https://fonts.googleapis.com/css2?family=Cinzel:wght@400;500&family=Open+Sans:wght@400&display=swap">
<style>
  :root {
    --backdrop: #ebe6de;
    --paper: #ffffff;
    --brand-blue: #2b8fd0;
    --band-blue: #2d95d3;
    --sky-blue: #56bfee;
    --text-white: #ffffff;
  }
  * { box-sizing: border-box; margin: 0; padding: 0; }
  html, body {
    width: 1200px;
    height: 981px;
    overflow: hidden;
    background: var(--backdrop);
  }
  .card {
    position: absolute;
    top: 40px;
    width: 506px;
    height: 882px;
    overflow: hidden;
  }
  .card-front { left: 55px; background: var(--paper); box-shadow: 0 2px 6px rgba(0,0,0,0.15); }
  .card-back { left: 620px; background: var(--sky-blue); box-shadow: 0 2px 6px rgba(0,0,0,0.15); }

  .front-wave { position: absolute; inset: 0; width: 506px; height: 882px; }

  .brand-name {
    position: absolute;
    left: 0; right: 0;
    top: 118px;
    text-align: center;
    font-family: "Cinzel", serif;
    font-weight: 500;
    font-size: 52px;
    line-height: 62px;
    letter-spacing: 1px;
    color: var(--brand-blue);
  }
  .tagline {
    position: absolute;
    left: 0; right: 0;
    top: 348px;
    text-align: center;
    font-family: "Cinzel", serif;
    font-weight: 500;
    font-size: 23px;
    line-height: 31px;
    color: var(--brand-blue);
  }
  .person-name {
    position: absolute;
    left: 0; right: 0;
    top: 482px;
    text-align: center;
    font-family: "Cinzel", serif;
    font-weight: 500;
    font-size: 29px;
    color: var(--brand-blue);
  }
  .person-title {
    position: absolute;
    left: 0; right: 0;
    top: 522px;
    text-align: center;
    font-family: "Cinzel", serif;
    font-size: 24px;
    letter-spacing: 3px;
    color: var(--brand-blue);
  }
  .contact-list {
    position: absolute;
    left: 0; right: 0;
    top: 702px;
    list-style: none;
    font-family: "Open Sans", sans-serif;
    font-size: 21px;
    color: var(--text-white);
  }
  .contact-item {
    display: flex;
    justify-content: center;
    align-items: center;
    gap: 10px;
    height: 45px;
  }
  .contact-icon { width: 16px; height: 16px; flex: none; }

  .back-brand {
    position: absolute;
    left: 0; right: 0;
    top: 300px;
    text-align: center;
    font-family: "Cinzel", serif;
    font-weight: 500;
    font-size: 52px;
    line-height: 62px;
    color: var(--text-white);
  }
  .back-website {
    position: absolute;
    left: 0; right: 0;
    top: 582px;
    text-align: center;
    font-family: "Open Sans", sans-serif;
    font-size: 21px;
    letter-spacing: 0.5px;
    color: var(--text-white);
  }
</style>
</head>
<body>
  <section class="card card-front">
    <svg class="front-wave" viewBox="0 0 506 882" aria-hidden="true">
      <path d="M0 664 Q253 530 506 664" fill="none" stroke="var(--sky-blue)" stroke-width="7"/>
      <path d="M0 694 Q253 536 506 694 V882 H0 Z" fill="var(--band-blue)"/>
    </svg>

    <h1 class="brand-name">Harborline<br>Renewal</h1>

    <p class="tagline">Specializing in<br>Water Damage Restoration</p>

    <h2 class="person-name">Darnell Quisby</h2>
    <p class="person-title">Title</p>

    <ul class="contact-list">
      <li class="contact-item">
        <svg class="contact-icon" viewBox="0 0 16 16" aria-hidden="true">
          <circle cx="8" cy="8" r="7" fill="none" stroke="#fff" stroke-width="1.3"/>
          <path d="M5.2 4.2 L6.6 4 L7.2 6 L6.3 6.8 Q7.2 8.8 9.2 9.7 L10 8.8 L12 9.4 L11.8 10.8 Q8 11.6 5 7.6 Q4.6 5.8 5.2 4.2 Z" fill="#fff"/>
        </svg>
        <span>555-318-2046</span>
      </li>
      <li class="contact-item">
        <svg class="contact-icon" viewBox="0 0 16 16" aria-hidden="true">
          <rect x="1.5" y="4" width="13" height="9" rx="1" fill="#fff"/>
          <path d="M1.5 4.5 L8 9 L14.5 4.5" fill="none" stroke="var(--band-blue)" stroke-width="1.2"/>
        </svg>
        <span>Darnell@HarborlineRenewal.example</span>
      </li>
      <li class="contact-item">
        <svg class="contact-icon" viewBox="0 0 16 16" aria-hidden="true">
          <g fill="none" stroke="#fff" stroke-width="1.2">
            <circle cx="8" cy="8" r="6.5"/>
            <ellipse cx="8" cy="8" rx="3" ry="6.5"/>
            <path d="M1.5 8 H14.5 M2.5 4.8 H13.5 M2.5 11.2 H13.5"/>
          </g>
        </svg>
        <span>www.HarborlineRenewal.example</span>
      </li>
    </ul>
  </section>

  <section class="card card-back">
    <p class="back-brand">Harborline<br>Renewal</p>
    <p class="back-website">www.HarborlineRenewal.example</p>
  </section>
</body>
</html>
```